Unique Business Card Design

Unique Business Card design for our orthotic and prosthetic company. Our logo is on our website, color is light blue. Unique shape (artificial leg shaped, vertical, etc..) preferred. Logo, business name, individual name and basic demographics needed.

Industry/Entity Type

Business

Contact Information for Business Card

Logo, Industry, Phone # Logo, "Prosthetic & Orthotic Services" Place to add individual name and contact info

Colors
cee9f5

Requirements
Must have
• The icon must be there, placement of "Prosthetic & Orthotic Services" can be moved
Nice to have
• Like the mix of light blue, and a little darker blue. One design included the icons from my website which was a nice touch

```html
<!DOCTYPE html>
<html lang="en">
<head>
<meta charset="utf-8">
<title>Limbwell Inc. Business Card</title>
<link rel="stylesheet" href="https://fonts.googleapis.com/css2?family=PT+Sans:wght@400;700&family=EB+Garamond:ital,wght@1,500&display=swap">
<style>
  :root {
    --page-bg: #c9c7c4;
    --card-top: #f4f5f7;
    --card-bottom: #e4e6ea;
    --navy: #253b80;
    --band-text: #cdd5ea;
    --ink: #2f3136;
    --emblem: #f1f2f4;
  }
  html, body {
    margin: 0;
    width: 1200px;
    height: 834px;
    overflow: hidden;
    background: var(--page-bg);
  }
  .card {
    position: absolute;
    left: 100px;
    top: 133px;
    width: 1000px;
    height: 568px;
    border-radius: 22px;
    background: linear-gradient(180deg, var(--card-top), var(--card-bottom));
    overflow: hidden;
    box-shadow: 0 6px 24px rgba(0,0,0,0.18);
    font-family: "PT Sans", Arial, sans-serif;
  }
  .company-name {
    position: absolute;
    left: 41px;
    top: 40px;
    margin: 0;
    font-size: 56px;
    line-height: 1;
    font-weight: 700;
    color: var(--navy);
    letter-spacing: 0.5px;
  }
  .company-rule {
    position: absolute;
    left: 41px;
    top: 104px;
    width: 477px;
    height: 3px;
    background: var(--navy);
  }
  .tagline {
    position: absolute;
    left: 41px;
    top: 110px;
    margin: 0;
    font-family: "EB Garamond", Georgia, serif;
    font-style: italic;
    font-weight: 500;
    font-size: 37px;
    line-height: 1.1;
    color: var(--navy);
  }
  .person-name {
    position: absolute;
    left: 53px;
    top: 176px;
    margin: 0;
    font-size: 31px;
    font-weight: 700;
    line-height: 1;
    color: var(--navy);
  }
  .person-name .credentials {
    font-size: 23px;
  }
  .person-email {
    position: absolute;
    left: 53px;
    top: 218px;
    font-size: 23px;
    line-height: 1;
    color: var(--ink);
  }
  .contact-band {
    position: absolute;
    left: 0;
    top: 269px;
    width: 1000px;
    height: 215px;
    background: var(--navy);
  }
  .contact-list {
    list-style: none;
    margin: 0;
    padding: 0;
    position: absolute;
    left: 62px;
    top: 33px;
  }
  .contact-item {
    display: flex;
    align-items: center;
    height: 38.5px;
    font-size: 23px;
    color: var(--band-text);
    letter-spacing: 0.3px;
  }
  .contact-item svg {
    width: 22px;
    height: 22px;
    margin-right: 18px;
    fill: var(--band-text);
  }
  .emblem {
    position: absolute;
    left: 688px;
    top: -1px;
    width: 224px;
    height: 224px;
    border-radius: 50%;
    background: var(--emblem);
  }
  .address {
    position: absolute;
    left: 53px;
    top: 508px;
    font-size: 23px;
    line-height: 1;
    color: var(--ink);
  }
</style>
</head>
<body>
  <div class="card">
    <h1 class="company-name">LIMBWELL INC.</h1>
    <div class="company-rule"></div>
    <p class="tagline">Prosthetic &amp; Orthotic Services</p>

    <h2 class="person-name">Miriam Kessler<span class="credentials">, CO LPO</span></h2>
    <div class="person-email">mkessler@limbwellinc.com</div>

    <div class="contact-band">
      <ul class="contact-list">
        <li class="contact-item">
          <svg viewBox="0 0 24 24" aria-hidden="true"><path d="M2 8c0-3 4-5 10-5s10 2 10 5v2h-5V8c-1-1-3-1.5-5-1.5S8 7 7 8v2H2z"/><path d="M5 12h14l2 9H3z M9 14a3 3 0 1 0 6 0a3 3 0 1 0-6 0z" fill-rule="evenodd"/></svg>
          555.201.4400
        </li>
        <li class="contact-item">
          <svg viewBox="0 0 24 24" aria-hidden="true"><path d="M7 1h10a2 2 0 0 1 2 2v18a2 2 0 0 1-2 2H7a2 2 0 0 1-2-2V3a2 2 0 0 1 2-2zm0 3v14h10V4zm5 15.5a1.2 1.2 0 1 0 0 2.4a1.2 1.2 0 1 0 0-2.4z" fill-rule="evenodd"/></svg>
          555.201.3187
        </li>
        <li class="contact-item">
          <svg viewBox="0 0 24 24" aria-hidden="true"><path d="M6 2h12v6H6z"/><path d="M2 9h20v9h-4v-3H6v3H2z"/><path d="M7 16h10v6H7z"/></svg>
          555-3908126
        </li>
        <li class="contact-item">
          <svg viewBox="0 0 24 24" aria-hidden="true"><path d="M12 1a11 11 0 1 0 0 22a11 11 0 1 0 0-22zm-2 4c2 1 1 3 3 3s2 2 0 3-4 0-4 3 3 2 3 5c-4 0-7-3-8-7 1-4 3-6 6-7zm7 3c2 1 3 3 3 5-1 1-2 0-3-1s-1-2 0-4z" fill-rule="evenodd"/></svg>
          www.limbwellinc.com
        </li>
      </ul>
      <div class="emblem"></div>
    </div>

    <div class="address">820 Harbor Ave., Millbrook, NY 10500</div>
  </div>
</body>
</html>
```